Business card design needed

I run a Beautician studio (for 7 years now)
I offer
- Velmo Body Sugaring
- Ruby Glaze
- Nails
- Facials
- Manicure
- Foot Treatment
It might not be necessary to list all those treatments?
Maybe the link to the Website is sufficient?
I leave that up to you ...
(more info on www.FernAndDewByLenka.com.au)
Velmo BodySugaring is our biggest success, It replaces waxing.
I would like to incorporate the logo into the Business Card.
We had many complaints regarding our old Business Cards as the Phone Number was to small.
On the backside, we would like a "your next Appointment" section.
Looking forward to you Design, cheers ... Lenka
Industry/Entity Type
Business
Contact Information for Business Card
Fern by Dew by Lenka
14 Korrin Sqr 3942 Berwick
www.FernAndDewByLenka.com.au
03 9481 2267

```html
<!DOCTYPE html>
<html lang="en">
<head>
<meta charset="utf-8">
<title>Velmo Body Sugaring – Business Cards</title>
<link rel="stylesheet" href="https://fonts.googleapis.com/css2?family=Cinzel:wght@500;600&family=Crimson+Text:wght@600;700&family=Source+Sans+3:wght@400;600;700&display=swap">
<style>
  :root {
    --backdrop: #1c1c1c;
    --card: #ffffff;
    --ink: #2b2b2b;
    --ink-soft: #444444;
    --green: #1f6b34;
    --green-swoosh: #1a8a3e;
    --orange: #e8562a;
    --amber: #f08a24;
    --yellow: #f5c51f;
    --sun: #f29a22;
    --rule: #9a9a9a;
    --box-line: #555555;
    --serif: "Cinzel", serif;
    --head: "Crimson Text", serif;
    --sans: "Source Sans 3", sans-serif;
  }
  * { box-sizing: border-box; margin: 0; padding: 0; }
  html, body { width: 1200px; height: 728px; overflow: hidden; background: var(--backdrop); }
  .sheet {
    position: relative; width: 1163px; height: 706px;
    transform: scale(1.0318, 1.0312); transform-origin: 0 0;
    font-family: var(--sans); color: var(--ink);
  }
  .card {
    position: absolute; width: 525px; height: 298px;
    background: var(--card); border-radius: 16px; overflow: hidden;
  }
  .card--front { left: 40px; top: 36px; }
  .card--back-top { left: 597px; top: 36px; }
  .card--hours { left: 42px; top: 368px; }
  .card--back-bottom { left: 606px; top: 372px; }

  /* brand name lockup */
  .brand { position: absolute; left: 0; right: 0; display: flex; flex-direction: column; align-items: center; }
  .brand__dot { width: 92px; height: 92px; border-radius: 50%; background: var(--sun); }
  .brand__name {
    margin-top: 18px; font-family: var(--serif); font-weight: 500;
    font-size: 22px; letter-spacing: 4px; color: var(--ink); text-transform: uppercase;
  }
  .card--front .brand { top: 36px; }
  .card--hours .brand { top: 22px; }

  /* front */
  .front-wave { position: absolute; inset: 0; }
  .front-contact {
    position: absolute; left: 28px; right: 20px; top: 236px;
    display: flex; color: #fff;
  }
  .front-contact__studio { padding-right: 10px; border-right: 1px solid rgba(255,255,255,.85); text-align: right; }
  .studio-name { font-family: var(--head); font-weight: 700; font-size: 18px; line-height: 22px; }
  .studio-address { font-family: var(--head); font-size: 13px; line-height: 20px; }
  .front-contact__lines { padding-left: 10px; }
  .phone { display: flex; align-items: center; gap: 6px; font-size: 18px; line-height: 24px; }
  .web { display: flex; align-items: center; gap: 8px; font-family: var(--head); font-size: 14px; line-height: 26px; }
  .icon { width: 14px; height: 14px; flex: none; }

  /* appointment backs */
  .appt__title {
    position: absolute; left: 34px; top: 50px;
    font-family: var(--head); font-weight: 600; font-size: 19px; color: var(--green); letter-spacing: .3px;
  }
  .appt__mark { position: absolute; left: 372px; top: 18px; width: 110px; display: flex; flex-direction: column; align-items: center; }
  .appt__mark .brand__dot { width: 40px; height: 40px; }
  .appt__mark .brand__name { margin-top: 8px; font-size: 7.5px; letter-spacing: 1.3px; white-space: nowrap; }
  .appt__watermark {
    position: absolute; left: 120px; top: 20px; width: 300px;
    display: flex; flex-direction: column; align-items: center; opacity: .08;
  }
  .appt__watermark .brand__dot { width: 150px; height: 150px; }
  .appt__watermark .brand__name { font-size: 30px; letter-spacing: 4px; white-space: nowrap; }
  .field { position: absolute; left: 34px; display: flex; align-items: flex-end; font-size: 15px; color: var(--ink-soft); }
  .field--name { top: 90px; }
  .field--date { top: 127px; }
  .field--next { top: 164px; }
  .line { display: inline-block; border-bottom: 1px solid var(--rule); height: 1px; margin-bottom: 5px; }
  .line--dotted { border-bottom-style: dotted; width: 258px; margin-left: 10px; }
  .line--date { width: 94px; margin: 0 6px 5px 26px; }
  .line--time { width: 90px; margin: 0 2px 5px 5px; }
  .box { display: inline-block; border: 1px solid var(--box-line); border-radius: 2px; }
  .box--wide { width: 94px; height: 20px; margin-left: 10px; }
  .box--wide + .box--wide { margin-left: 32px; }
  .days { position: absolute; left: 31px; top: 200px; display: flex; align-items: center; }
  .day { font-weight: 700; font-size: 15px; color: var(--ink-soft); margin-right: 9px; }
  .box--day { width: 33px; height: 19px; margin-right: 7px; }
  .appt__note { position: absolute; left: 30px; right: 30px; top: 249px; font-size: 13px; line-height: 18px; color: var(--ink); }

  /* hours */
  .hours-web {
    position: absolute; left: 0; right: 0; top: 201px; text-align: center;
    font-size: 13.5px; letter-spacing: 2.2px; color: var(--ink);
  }
  .hours-title {
    position: absolute; left: 0; right: 0; top: 233px; text-align: center;
    font-weight: 700; font-size: 20px; letter-spacing: 1.2px; color: #4a4a4a;
  }
  .hours-times {
    position: absolute; left: 0; right: 0; top: 267px; text-align: center;
    font-weight: 600; font-size: 15px; color: #4a4a4a;
  }
  .hours-times__sep { color: #aaa; margin: 0 6px; font-weight: 400; }
</style>
</head>
<body>
<main class="sheet">

  <section class="card card--front">
    <svg class="front-wave" viewBox="0 0 525 298" aria-hidden="true">
      <defs>
        <linearGradient id="front-band" x1="0" x2="1" y1="0" y2="0">
          <stop offset="0" stop-color="#e8562a"/>
          <stop offset=".55" stop-color="#f08a24"/>
          <stop offset="1" stop-color="#f5c51f"/>
        </linearGradient>
      </defs>
      <path d="M0,190 C130,250 330,260 525,168 L525,298 L0,298 Z" fill="url(#front-band)"/>
      <path d="M0,137 C120,205 300,228 430,206 C300,218 120,200 0,160 Z" fill="var(--green-swoosh)"/>
      <path d="M0,160 C120,200 300,218 430,206 C300,224 130,215 0,190 Z" fill="#fff"/>
    </svg>
    <div class="brand">
      <span class="brand__dot"></span>
      <span class="brand__name">Velmo Body Sugaring</span>
    </div>
    <div class="front-contact">
      <div class="front-contact__studio">
        <p class="studio-name">Fern by Dew by Lenka</p>
        <p class="studio-address">14 Korrin Sqr 3942 Berwick</p>
      </div>
      <div class="front-contact__lines">
        <p class="phone">
          <svg class="icon" viewBox="0 0 16 16" aria-hidden="true"><circle cx="8" cy="8" r="7" fill="none" stroke="#fff" stroke-width="1.2"/><path d="M5.5 4.5l1.3 1.6-.8.9c.5 1.1 1.3 1.9 2.4 2.4l.9-.8 1.6 1.3-.9 1.2c-2.6-.4-4.6-2.4-5-5z" fill="#fff"/></svg>
          03 9481 2267
        </p>
        <p class="web">
          <svg class="icon" viewBox="0 0 16 16" aria-hidden="true"><g fill="none" stroke="#fff" stroke-width="1"><circle cx="8" cy="8" r="6.5"/><ellipse cx="8" cy="8" rx="3" ry="6.5"/><path d="M1.5 8h13M2.5 4.8h11M2.5 11.2h11"/></g></svg>
          www.FernAndDewByLenka.com.au
        </p>
      </div>
    </div>
  </section>

  <section class="card card--back-top appt">
    <h2 class="appt__title">YOUR APPOINTMENT</h2>
    <div class="appt__mark">
      <span class="brand__dot"></span>
      <span class="brand__name">Velmo Body Sugaring</span>
    </div>
    <p class="field field--name">Name :<span class="line line--dotted"></span></p>
    <p class="field field--date">Date :<span class="line line--date"></span>Time :<span class="line line--time"></span>am / pm</p>
    <p class="field field--next">Next Appointment<span class="box box--wide"></span><span class="box box--wide"></span></p>
    <div class="days">
      <span class="day">MON</span><span class="box box--day"></span>
      <span class="day">TUE</span><span class="box box--day"></span>
      <span class="day">WED</span><span class="box box--day"></span>
      <span class="day">THU</span><span class="box box--day"></span>
      <span class="day">FRI</span><span class="box box--day"></span>
      <span class="day">SAT</span><span class="box box--day"></span>
    </div>
    <p class="appt__note">It would be appreciated if 24 hours notice could be given if you are unable to attend an appointment</p>
  </section>

  <section class="card card--hours">
    <div class="brand">
      <span class="brand__dot"></span>
      <span class="brand__name">Velmo Body Sugaring</span>
    </div>
    <p class="hours-web">www.FernAndDewByLenka.com.au</p>
    <h2 class="hours-title">Hours of Operation</h2>
    <p class="hours-times">Mon - Fri: 7.30am - 7.00pm<span class="hours-times__sep">|</span>Saturday: 7.30am - 12.00pm</p>
  </section>

  <section class="card card--back-bottom appt">
    <div class="appt__watermark" aria-hidden="true">
      <span class="brand__dot"></span>
      <span class="brand__name">Velmo Body Sugaring</span>
    </div>
    <h2 class="appt__title">YOUR APPOINTMENT</h2>
    <p class="field field--name">Name :<span class="line line--dotted"></span></p>
    <p class="field field--date">Date :<span class="line line--date"></span>Time :<span class="line line--time"></span>am / pm</p>
    <p class="field field--next">Next Appointment<span class="box box--wide"></span><span class="box box--wide"></span></p>
    <div class="days">
      <span class="day">MON</span><span class="box box--day"></span>
      <span class="day">TUE</span><span class="box box--day"></span>
      <span class="day">WED</span><span class="box box--day"></span>
      <span class="day">THU</span><span class="box box--day"></span>
      <span class="day">FRI</span><span class="box box--day"></span>
      <span class="day">SAT</span><span class="box box--day"></span>
    </div>
    <p class="appt__note">It would be appreciated if 24 hours notice could be given if you are unable to attend an appointment</p>
  </section>

</main>
</body>
</html>
```